Ridgeline Journeys business card

please see website
www.ridgelinejourneys.comau

info needed on card
Curtis Halvey
Ph
email
Adventure Riding GPS trails

please use my logo and colours off my site

Curtis Halvey
curtis@ridgelinejourneys.com

```html
<!DOCTYPE html>
<html lang="en">
<head>
<meta charset="utf-8">
<title>Ridgeline Journeys – Business Card</title>
<link rel="stylesheet" href="https://fonts.googleapis.com/css2?family=Oswald:wght@700&family=Open+Sans:wght@400;700&display=swap">
<style>
  :root {
    --page: #e9e6e1;
    --card: #f7f7f6;
    --ink: #1d1d1d;
    --band-dark: #151515;
    --band-grey: #b9b9b9;
    --accent: #f2dd2e;
    --white: #ffffff;
  }
  * { box-sizing: border-box; margin: 0; padding: 0; }
  html, body { width: 1200px; height: 902px; overflow: hidden; background: var(--page); }
  .sheet { position: relative; width: 1200px; height: 902px; }

  .card {
    position: absolute;
    width: 540px;
    height: 310px;
    background: var(--card);
    border-radius: 3px;
    box-shadow: 0 2px 6px rgba(0,0,0,0.18);
    overflow: hidden;
  }
  .card--front { left: 40px; top: 296px; }
  .card--back  { left: 620px; top: 296px; }

  .brand {
    display: flex;
    align-items: center;
    gap: 16px;
    font-family: "Oswald", sans-serif;
    font-weight: 700;
    text-transform: uppercase;
    color: var(--ink);
    line-height: 1;
  }
  .brand__square { width: 44px; height: 44px; background: var(--accent); flex: none; }
  .brand__name { display: flex; flex-direction: column; }

  .card--front .brand {
    position: absolute; left: 50%; top: 50%;
    transform: translate(-50%, -50%);
    font-size: 44px;
  }
  .card--front .brand__square { width: 62px; height: 62px; }

  .card--back .brand {
    position: absolute; left: 170px; top: 40px;
    font-size: 32px;
  }

  .back__bands { position: absolute; inset: 0; }

  .contact {
    position: absolute;
    left: 0; right: 0; top: 196px;
    font-family: "Open Sans", sans-serif;
    color: var(--white);
    text-align: center;
  }
  .contact__name {
    display: flex; align-items: center; justify-content: center; gap: 14px;
    font-size: 22px; font-weight: 400; letter-spacing: 0.5px;
    margin-bottom: 8px;
  }
  .contact__rule { width: 70px; height: 1px; background: var(--band-grey); }
  .contact__line { font-size: 15px; font-weight: 700; line-height: 1.45; }
</style>
</head>
<body>
<main class="sheet">

  <section class="card card--front" aria-label="Card front">
    <div class="brand">
      <span class="brand__square"></span>
      <span class="brand__name"><span>Ridgeline</span><span>Journeys</span></span>
    </div>
  </section>

  <section class="card card--back" aria-label="Card back">
    <svg class="back__bands" width="540" height="310" viewBox="0 0 540 310" aria-hidden="true">
      <path d="M0 232 Q280 150 540 104 L540 310 L0 310 Z" fill="var(--band-grey)"/>
      <path d="M0 246 Q280 164 540 118 L540 310 L0 310 Z" fill="var(--band-dark)"/>
    </svg>
    <div class="brand">
      <span class="brand__square"></span>
      <span class="brand__name"><span>Ridgeline</span><span>Journeys</span></span>
    </div>
    <div class="contact">
      <p class="contact__name"><span class="contact__rule"></span>Curtis Halvey<span class="contact__rule"></span></p>
      <p class="contact__line">curtis@ridgelinejourneys.com</p>
      <p class="contact__line">www.ridgelinejourneys.com.au</p>
    </div>
  </section>

</main>
</body>
</html>
```